business card deign

Logo needs the following on it.
1. attached logo
2. Tagline - "From the first cooler to the last song...we bring it all!"
3. Name- Dalton Pikes, Founder and CPO
4. Address - 412 E. Carver Avenue, Ste 2207, Tampa, FL. 33917
5. Phone - 555.318.4726

```html
<!DOCTYPE html>
<html lang="en">
<head>
<meta charset="utf-8">
<title>Hopline Business Card</title>
<link href="https://fonts.googleapis.com/css2?family=Montserrat:wght@400;700&display=swap" rel="stylesheet">
<style>
  :root {
    --stage: #3a3a3a;
    --ink: #000000;
    --paper: #ffffff;
    --muted: #333333;
  }
  * { margin: 0; padding: 0; box-sizing: border-box; }
  html, body {
    width: 1200px;
    height: 689px;
    overflow: hidden;
    background: var(--stage);
    font-family: "Montserrat", sans-serif;
  }
  .canvas {
    width: 1200px;
    height: 689px;
    display: flex;
    align-items: center;
    justify-content: center;
    gap: 40px;
  }
  .card {
    width: 540px;
    height: 309px;
    border-radius: 22px;
    position: relative;
    overflow: hidden;
  }
  .card-front {
    background: var(--ink);
    display: flex;
    flex-direction: column;
    align-items: center;
    justify-content: center;
  }
  .brand-mark {
    width: 120px;
    height: 120px;
    border-radius: 50%;
    background: var(--paper);
    margin-bottom: 26px;
  }
  .brand-name {
    color: var(--paper);
    font-weight: 700;
    font-size: 44px;
    letter-spacing: 18px;
    padding-left: 18px;
  }
  .card-back {
    background: var(--paper);
  }
  .identity {
    position: absolute;
    left: 70px;
    top: 98px;
    width: 200px;
    text-align: right;
  }
  .person-name {
    font-weight: 700;
    font-size: 22px;
    color: var(--ink);
    white-space: nowrap;
  }
  .person-title {
    font-size: 14px;
    color: var(--muted);
    margin-top: 2px;
  }
  .divider {
    position: absolute;
    left: 290px;
    top: 70px;
    width: 1px;
    height: 100px;
    background: var(--ink);
  }
  .contact {
    position: absolute;
    left: 308px;
    top: 74px;
    font-size: 13px;
    color: var(--muted);
    line-height: 1.35;
    white-space: nowrap;
  }
  .contact-phone {
    display: flex;
    align-items: center;
    gap: 6px;
    margin-bottom: 14px;
  }
  .contact-phone svg { width: 12px; height: 12px; }
  .tagline-band {
    position: absolute;
    left: 0;
    right: 0;
    bottom: 34px;
    height: 28px;
    background: var(--ink);
    color: var(--paper);
    font-size: 12.5px;
    display: flex;
    align-items: center;
    padding-left: 62px;
    white-space: nowrap;
  }
  .band-brand {
    position: absolute;
    right: 22px;
    bottom: 68px;
    font-weight: 700;
    font-size: 11px;
    letter-spacing: 2px;
    color: var(--ink);
  }
</style>
</head>
<body>
  <main class="canvas">
    <section class="card card-front">
      <div class="brand-mark"></div>
      <div class="brand-name">HOPLINE</div>
    </section>

    <section class="card card-back">
      <div class="identity">
        <div class="person-name">Dalton Pikes</div>
        <div class="person-title">Founder and CPO</div>
      </div>
      <div class="divider"></div>
      <div class="contact">
        <div class="contact-phone">
          <svg viewBox="0 0 24 24" aria-hidden="true"><path fill="#000" d="M6.6 10.8a15.1 15.1 0 0 0 6.6 6.6l2.2-2.2c.3-.3.7-.4 1-.2 1.1.4 2.3.6 3.6.6.6 0 1 .4 1 1V20c0 .6-.4 1-1 1C10.6 21 3 13.4 3 4c0-.6.4-1 1-1h3.5c.6 0 1 .4 1 1 0 1.3.2 2.5.6 3.6.1.3 0 .7-.2 1z"/></svg>
          <span>555.318.4726</span>
        </div>
        <div class="contact-address">412 E. Carver Avenue, Ste<br>2207, Tampa, FL. 33917</div>
      </div>
      <div class="band-brand">HOPLINE</div>
      <div class="tagline-band">From the first cooler to the last song...we bring it all!</div>
    </section>
  </main>
</body>
</html>
```